Business card design and logo for hot water plumbing business

I need a logo and business card for my business which installs hot water heaters
Must have on front:
Bramblefield Hot Water Solutions
Gareth Pennick
0417382946

Either front or back:
gareth@bramblefieldhotwatersolutions.com.au
ABN 48276153094
Licence No 583214K

On the back in point form:
Supply and installation of
• electric storage
• gas storage/instantaneous
• heat pumps
• solar heaters

Iv provided 3 examples of cards I like but open to different ideas.

```html
<!DOCTYPE html>
<html lang="en">
<head>
<meta charset="utf-8">
<title>Bramblefield Hot Water Solutions – Business Card</title>
<link href="https://fonts.googleapis.com/css2?family=Exo+2:wght@400;600;800&display=swap" rel="stylesheet">
<style>
  :root {
    --backdrop: #2c2c2e;
    --card: #f4f5f6;
    --navy: #233848;
    --cyan: #1ccbe6;
    --muted: #5b6b78;
    --white: #ffffff;
  }
  * { box-sizing: border-box; margin: 0; padding: 0; }
  html, body {
    width: 1200px; height: 892px; overflow: hidden;
    background: var(--backdrop);
    font-family: "Exo 2", sans-serif;
  }
  .stage { position: relative; width: 1200px; height: 892px; }
  .card {
    position: absolute; left: 250px; width: 700px; height: 390px;
    background: var(--card); border-radius: 4px; overflow: hidden;
    box-shadow: 0 10px 30px rgba(0,0,0,.45);
  }
  .card--front { top: 30px; }
  .card--back { top: 470px; }

  .logo { display: flex; flex-direction: column; align-items: center; text-align: center; }
  .logo__lockup { display: flex; align-items: center; gap: 12px; }
  .logo__mark { width: 46px; height: 46px; border-radius: 50%; background: var(--cyan); flex: none; }
  .logo__name {
    color: var(--navy); font-weight: 800; font-size: 22px; line-height: 1.05;
    text-transform: uppercase; letter-spacing: .5px; text-align: left;
  }
  .logo__tagline { margin-top: 8px; font-size: 9px; color: var(--muted); letter-spacing: .3px; }

  .card--front .logo { position: absolute; left: 0; top: 0; width: 340px; height: 390px; justify-content: center; }

  .details { position: absolute; left: 350px; top: 24px; width: 326px; }
  .name-panel {
    height: 100px; border-radius: 10px; background: var(--cyan);
    padding: 18px 22px; color: var(--white);
  }
  .name-panel__name { font-size: 32px; font-weight: 600; letter-spacing: 1.5px; text-transform: uppercase; line-height: 1.1; }
  .name-panel__role { margin-top: 6px; font-size: 13px; color: var(--navy); opacity: .85; }

  .info-row {
    margin-top: 10px; height: 70px; border-radius: 10px; background: var(--navy);
    display: flex; align-items: center; justify-content: space-between;
    padding: 0 14px 0 20px; color: var(--white); font-size: 13.5px; line-height: 1.45;
  }
  .info-row--email { font-size: 12px; }
  .info-row__icon { width: 26px; height: 26px; flex: none; margin-left: 10px; }

  .card--back .logo { position: absolute; left: 0; top: 44px; width: 700px; }
  .services {
    position: absolute; left: 0; top: 182px; width: 700px;
    display: flex; flex-direction: column; align-items: center;
    color: var(--navy);
  }
  .services__title { font-size: 15px; font-weight: 600; letter-spacing: .5px; }
  .services__list {
    list-style: none; margin-top: 12px;
    display: grid; grid-template-columns: 220px 260px; row-gap: 8px; column-gap: 20px;
    font-size: 14px;
  }
  .services__item { display: flex; align-items: center; gap: 10px; }
  .services__item::before {
    content: ""; width: 8px; height: 8px; border-radius: 50%;
    background: var(--cyan); flex: none;
  }
  .back-band {
    position: absolute; left: 0; bottom: 0; width: 700px; height: 70px;
    background: var(--navy); color: var(--white);
    display: flex; align-items: center; padding-left: 30px;
    font-size: 17px; letter-spacing: 1px;
  }
</style>
</head>
<body>
<main class="stage">

  <section class="card card--front" aria-label="Business card front">
    <div class="logo">
      <div class="logo__lockup">
        <span class="logo__mark"></span>
        <span class="logo__name">Bramblefield<br>Hot Water<br>Solutions</span>
      </div>
      <p class="logo__tagline">Reliable hot water installation and repair services</p>
    </div>

    <div class="details">
      <div class="name-panel">
        <p class="name-panel__name">Gareth Pennick</p>
        <p class="name-panel__role">Hot Water Technician</p>
      </div>

      <div class="info-row info-row--address">
        <span>19 Kestrel Road,<br>Unit 3 Harbour St W.</span>
        <svg class="info-row__icon" viewBox="0 0 24 24" aria-hidden="true">
          <path d="M3 12 12 4l9 8" fill="none" stroke="#fff" stroke-width="2.2" stroke-linejoin="round"/>
          <path d="M6 11v9h4v-5h4v5h4v-9" fill="#fff"/>
        </svg>
      </div>

      <div class="info-row info-row--phone">
        <span>0417 382 946<br>ABN 48276153094 · Lic 583214K</span>
        <svg class="info-row__icon" viewBox="0 0 24 24" aria-hidden="true">
          <path d="M6.6 10.8c1.4 2.8 3.8 5.1 6.6 6.6l2.2-2.2c.3-.3.7-.4 1-.2 1.1.4 2.3.6 3.6.6.6 0 1 .4 1 1V20c0 .6-.4 1-1 1C10.6 21 3 13.4 3 4c0-.6.4-1 1-1h3.5c.6 0 1 .4 1 1 0 1.3.2 2.5.6 3.6.1.3 0 .7-.2 1z" fill="#fff"/>
        </svg>
      </div>

      <div class="info-row info-row--email">
        <span>gareth@bramblefieldhotwatersolutions.com.au<br>www.bramblefieldhotwater.com.au</span>
        <svg class="info-row__icon" viewBox="0 0 24 24" aria-hidden="true">
          <rect x="3" y="5" width="18" height="12" rx="1.5" fill="none" stroke="#fff" stroke-width="2"/>
          <path d="M9 20h6" stroke="#fff" stroke-width="2" stroke-linecap="round"/>
        </svg>
      </div>
    </div>
  </section>

  <section class="card card--back" aria-label="Business card back">
    <div class="logo">
      <div class="logo__lockup">
        <span class="logo__mark"></span>
        <span class="logo__name">Bramblefield<br>Hot Water<br>Solutions</span>
      </div>
      <p class="logo__tagline">Reliable hot water installation and repair services</p>
    </div>

    <div class="services">
      <p class="services__title">Supply and installation of</p>
      <ul class="services__list">
        <li class="services__item">electric storage</li>
        <li class="services__item">gas storage/instantaneous</li>
        <li class="services__item">heat pumps</li>
        <li class="services__item">solar heaters</li>
      </ul>
    </div>

    <div class="back-band">www.bramblefieldhotwater.com.au</div>
  </section>

</main>
</body>
</html>
```